CrestwayGuide,Christian faith-based firm providing personal,professional & organizational consulting

2 designs needed for retractable signs (size 33.5" x 79"):
1. For Firm (CrestwayGuide)
We believe:
*That not-for-profit organizations make the most important investments in changing lives and transforming communities
*That vision must be at the core of every organization;
*That organizational outcomes should be transformative;
*That impactful leadership is driven and directed by vision clarity, vision strategy, and vision execution; and
*That organizational insight and collaborative strategy results in sound solutions.

Services Provided:
As a full service and comprehensive firm, our capabilities include:
*Vision Discovery, Clarity and Execution
*Organizational Strategy Formation, Action Planning and Execution
*Leadership Excellence and Team Development
*Retreats, Conferences and Workshops for capacity building
*Executive and Administrative Services
*Project Planning, Management and Synergy

2. For the Women's Retreat the Firm hosts annually (Gentle and Gathered In Women's Retreat)
This ministry is established to facilitate and be a conduit by which women are empowered in their Personal, Professional, and Spiritual lives to fulfill the best that God has designed for them".

Target Market(s)

Professionals, Non-Profit, Faith Based Organizations - CrestwayGuide sign
Faith Based women, diverse, multi-cultural - Gentle and Gathered In sign

Font styles to use
Serif

Colors
fbed22
ffffff
1b1b1b

Requirements
Must have
• Use of logos, colors to include firm colors of black, gold and white (all or in part).
• 1. CrestwayGuide design - the words and images for
• i. VISION
• ii. ORGANIZATIONAL STRATEGY
• iii. LEADERSHIP DEVELOPMENT
• iv. PROJECT PLANNING & MANAGEMENT
• (www.crestwayguide.example)
• 2. Gentle and Gathered In design - incorporate images and words to reflect-"Gentle and Gathered In. Is a part of the Women's Ministry arm of CrestwayGuide, Inc. This ministry is established to facilitate and be a conduit by which women are EMPOWERED in their Personal, Professional, and Spiritual lives to fulfill the best that God has designed for them".

```html
<!DOCTYPE html>
<html lang="en">
<head>
<meta charset="utf-8">
<title>CrestwayGuide Retractable Signs</title>
<link rel="stylesheet" href="https://fonts.googleapis.com/css2?family=Tinos:wght@400;700&display=swap">
<style>
  :root {
    --page: #e9e9ec;
    --gold: #86744a;
    --charcoal: #4a4740;
    --ink: #1b1b1b;
    --white: #ffffff;
    --serif: "Tinos", "Times New Roman", serif;
  }
  * { margin: 0; padding: 0; box-sizing: border-box; }
  html, body { width: 1200px; height: 1200px; overflow: hidden; }
  body {
    background: var(--page);
    font-family: var(--serif);
    position: relative;
  }
  .sign {
    position: absolute;
    top: 120px;
    width: 400px;
    height: 960px;
    overflow: hidden;
    background: var(--gold);
    box-shadow: 0 6px 24px rgba(0,0,0,0.12);
  }
  .sign--firm { left: 150px; }
  .sign--retreat { left: 650px; }
  .sign__art { position: absolute; inset: 0; width: 400px; height: 960px; }
  .line {
    position: absolute;
    left: 0;
    width: 100%;
    text-align: center;
    color: var(--white);
    line-height: 1;
    white-space: nowrap;
  }
  .line--bold { font-weight: 700; }

  /* Firm sign */
  .firm-name {
    position: absolute; top: 130px; left: 0; width: 100%;
    text-align: center; font-size: 44px; color: var(--ink); line-height: 1;
  }
  .firm-url { color: var(--white); font-size: 23px; }

  /* Retreat sign */
  .retreat-name {
    position: absolute; top: 96px; left: 20px; width: 200px;
    text-align: center; font-size: 26px; line-height: 1.15; color: var(--charcoal);
  }
</style>
</head>
<body>

<section class="sign sign--firm" aria-label="CrestwayGuide sign">
  <svg class="sign__art" viewBox="0 0 400 960">
    <defs>
      <linearGradient id="stairsTone" x1="0" y1="0" x2="0" y2="1">
        <stop offset="0" stop-color="#fbfbfa"/>
        <stop offset="0.35" stop-color="#ece9e4"/>
        <stop offset="0.55" stop-color="#b9bcbb"/>
        <stop offset="0.75" stop-color="#4c5d62"/>
        <stop offset="1" stop-color="#1f2e33"/>
      </linearGradient>
    </defs>
    <rect class="photo" x="0" y="0" width="400" height="560" fill="url(#stairsTone)" role="img" aria-label="Photo of a man in a suit climbing a long staircase toward the light"/>
    <path class="swoosh" d="M0 419 Q150 640 400 411 L400 960 L0 960 Z" fill="var(--charcoal)"/>
    <path class="gold-field" d="M0 467 Q170 620 400 427 L400 960 L0 960 Z" fill="var(--gold)"/>
    <rect class="footer-band" x="0" y="880" width="400" height="80" fill="var(--charcoal)"/>
  </svg>

  <div class="firm-name">CrestwayGuide</div>

  <div class="line" style="top:556px;font-size:57px;">VISION</div>
  <div class="line" style="top:629px;font-size:29px;">ORGANIZATIONAL</div>
  <div class="line line--bold" style="top:660px;font-size:36px;">STRATEGY</div>
  <div class="line line--bold" style="top:714px;font-size:36px;">LEADERSHIP</div>
  <div class="line" style="top:749px;font-size:32px;">DEVELOPMENT</div>
  <div class="line" style="top:800px;font-size:30px;">PROJECT PLANNING &amp;</div>
  <div class="line line--bold" style="top:831px;font-size:31px;">MANAGEMENT</div>
  <div class="line firm-url" style="top:896px;">www.crestwayguide.example</div>
</section>

<section class="sign sign--retreat" aria-label="Gentle and Gathered In sign">
  <svg class="sign__art" viewBox="0 0 400 960">
    <defs>
      <linearGradient id="portraitTone" x1="0" y1="0" x2="1" y2="0">
        <stop offset="0" stop-color="#e6e6e4"/>
        <stop offset="0.45" stop-color="#d8d6d2"/>
        <stop offset="0.7" stop-color="#6b4a35"/>
        <stop offset="1" stop-color="#2d221c"/>
      </linearGradient>
    </defs>
    <rect class="photo" x="0" y="0" width="400" height="480" fill="url(#portraitTone)" role="img" aria-label="Photo of a joyful woman with curly hair, eyes closed, hand on her heart, against a white brick wall"/>
    <path class="swoosh" d="M0 368 Q160 590 400 339 L400 960 L0 960 Z" fill="var(--charcoal)"/>
    <path class="gold-field" d="M0 417 Q170 590 400 351 L400 960 L0 960 Z" fill="var(--gold)"/>
    <rect class="footer-strip" x="0" y="947" width="400" height="13" fill="var(--charcoal)"/>
  </svg>

  <div class="retreat-name">Gentle and Gathered In</div>

  <div class="line" style="top:519px;font-size:33px;">Through This Ministry,</div>
  <div class="line" style="top:573px;font-size:44px;">Women are</div>
  <div class="line line--bold" style="top:621px;font-size:48px;">EMPOWERED</div>
  <div class="line" style="top:676px;font-size:44px;">in their:</div>
  <div class="line line--bold" style="top:729px;font-size:43px;">Personal</div>
  <div class="line line--bold" style="top:775px;font-size:43px;">Professional</div>
  <div class="line" style="top:823px;font-size:43px;">and</div>
  <div class="line line--bold" style="top:871px;font-size:43px;">Spiritual lives</div>
</section>

</body>
</html>
```